Website for Excavator and Earthworks Company

We require a modern, sleek and practical website for our newly created earthworks/excavator business in Perth, Western Australia called Bluegum Ridge Earthworks.

The website should have a modern, cutting edge feel but only needs to be relatively simplistic in it's layout and eventual functionality.

Some pages it should have would be Home, About, Projects and Contact Us.

```html
<!DOCTYPE html>
<html lang="en">
<head>
<meta charset="utf-8">
<title>Bluegum Ridge Earthworks</title>
<link href="https://fonts.googleapis.com/css2?family=Orbitron:wght@500;700;800&family=Quicksand:wght@400;500;600;700&display=swap" rel="stylesheet">
<style>
:root{
  --lime:#b2d012;
  --lime-dark:#93ad08;
  --ink:#0b0b0b;
  --ink-soft:#1c1c1c;
  --text:#333;
  --muted:#6b6b6b;
  --paper:#ffffff;
  --mist:#f2f4ee;
  --line:#dcdcdc;
}
*{box-sizing:border-box;margin:0;padding:0}
html,body{width:1200px;height:5056px;overflow:hidden}
body{font-family:"Quicksand",sans-serif;color:var(--text);background:var(--paper);position:relative}
.heading-font{font-family:"Orbitron",sans-serif}
a{color:inherit;text-decoration:none}

/* header */
.site-header{position:absolute;top:0;left:0;width:1200px;height:80px;display:flex;align-items:center;justify-content:space-between;padding:0 60px 0 112px;background:var(--paper)}
.brand{display:flex;align-items:center;gap:12px;font-family:"Orbitron",sans-serif;font-weight:800;font-size:22px;color:var(--ink);line-height:1}
.brand-square{width:34px;height:34px;background:var(--lime)}
.main-nav{display:flex;align-items:center;gap:34px;font-weight:600;font-size:17px;color:var(--ink)}
.nav-cta{background:var(--lime);padding:10px 26px;border-radius:4px 16px 4px 16px;color:var(--ink)}

/* hero */
.hero{position:absolute;top:80px;left:0;width:1200px;height:560px}
.hero-photo{position:absolute;inset:0;background:linear-gradient(180deg,#3a6fa8 0%,#7ea4c9 30%,#9a8c6e 62%,#5d5444 100%)}
.hero-curve{position:absolute;left:0;bottom:0;width:1200px;height:160px}
.scroll-cue{position:absolute;left:582px;top:488px;width:36px;height:36px;border-radius:50%;background:var(--paper);border:2px solid var(--lime);display:flex;align-items:center;justify-content:center}

/* shared section titles */
.section-title{position:absolute;left:0;width:1200px;text-align:center}
.section-title .mark{display:block;margin:0 auto 6px;width:20px;height:20px;background:var(--lime)}
.section-title h2{display:inline-flex;align-items:center;gap:18px;font-family:"Orbitron",sans-serif;font-weight:700;font-size:38px;color:var(--ink)}
.section-title h2::before,.section-title h2::after{content:"";width:90px;height:3px;background:currentColor}
.section-title.on-dark h2{color:#fff}

/* about */
.about{position:absolute;top:660px;left:0;width:1200px;height:560px}
.about-copy{position:absolute;left:112px;top:112px;width:430px}
.about-copy h2{font-family:"Orbitron",sans-serif;font-weight:700;font-size:34px;line-height:1.2;color:var(--ink)}
.about-copy h2::after{content:"";display:block;width:120px;height:3px;background:var(--ink);margin-top:12px}
.about-copy p{font-size:14px;line-height:1.6;margin-top:18px;color:var(--muted)}
.btn-lime{display:inline-block;background:var(--lime);color:var(--ink);font-weight:700;font-size:16px;padding:10px 30px;border-radius:4px 18px 4px 18px}
.about-copy .btn-lime{margin-top:44px}
.about-photo{position:absolute;background:linear-gradient(160deg,#6b5a42,#a38d67 55%,#4b5a3c)}
.about-photo.a1{left:608px;top:112px;width:232px;height:320px}
.about-photo.a2{left:870px;top:112px;width:190px;height:320px;background:linear-gradient(160deg,#8a7a5b,#c49a2a 45%,#5a4a35)}
.about-badge{position:absolute;left:808px;top:236px;width:64px;height:64px;background:var(--lime);border:4px solid #fff}

/* values */
.values{position:absolute;top:1260px;left:0;width:1200px;height:620px;background:var(--mist)}
.values .section-title{top:100px}
.value-cards{position:absolute;top:240px;left:112px;display:flex;gap:24px}
.value-card{width:222px;height:220px;background:#fff;box-shadow:0 4px 14px rgba(0,0,0,.12);text-align:center;padding:24px 18px}
.value-card.is-active{border-bottom:6px solid var(--lime);transform:translateY(-10px)}
.value-icon{width:52px;height:52px;border-radius:50%;background:var(--lime);margin:0 auto 14px;display:flex;align-items:center;justify-content:center}
.value-card h3{font-family:"Orbitron",sans-serif;font-size:14px;line-height:1.3;color:var(--ink);font-weight:700}
.value-card p{font-size:12.5px;line-height:1.5;color:var(--muted);margin-top:12px}
.values-band{position:absolute;left:0;bottom:-2px;width:1200px;height:100px}

/* why */
.why{position:absolute;top:1880px;left:0;width:1200px;height:560px;background:var(--ink)}
.why-top{position:absolute;left:0;top:0;width:1200px;height:60px}
.why .section-title{top:56px}
.why-mark{position:absolute;left:450px;top:160px;width:300px;height:300px;border-radius:50%;background:var(--lime);display:flex;align-items:center;justify-content:center;text-align:center;font-family:"Orbitron",sans-serif;font-weight:800;font-size:30px;line-height:1.2;color:var(--ink)}
.why-item{position:absolute;width:300px;display:flex;align-items:flex-start;gap:16px;color:#fff}
.why-item.left{left:112px;flex-direction:row-reverse;text-align:right}
.why-item.right{left:820px}
.why-item h3{font-family:"Orbitron",sans-serif;font-size:19px;line-height:1.25;font-weight:700}
.why-item p{font-size:13px;line-height:1.5;color:#cfcfcf;margin-top:6px}
.why-icon{flex:none;width:60px;height:60px;border-radius:50%;border:2px solid var(--lime);display:flex;align-items:center;justify-content:center}

/* services */
.services{position:absolute;top:2440px;left:0;width:1200px;height:660px;background:#fff}
.services .section-title{top:90px}
.service-cards{position:absolute;top:190px;left:108px;display:flex;gap:28px}
.service-card{width:310px;height:360px;background:#fff;box-shadow:0 4px 14px rgba(0,0,0,.14);text-align:center;position:relative}
.service-photo{height:200px;background:linear-gradient(170deg,#8ab0d6,#a0876a 55%,#6a5a45)}
.service-card:nth-child(2) .service-photo{background:linear-gradient(170deg,#c0703a,#8c6a4a 50%,#4d3d30)}
.service-card:nth-child(3) .service-photo{background:linear-gradient(170deg,#d2b68a,#b27a2a 50%,#5a4632)}
.service-icon{position:absolute;left:129px;top:174px;width:52px;height:52px;border-radius:50%;background:var(--lime);border:4px solid #fff}
.service-card h3{font-family:"Orbitron",sans-serif;font-size:15px;font-weight:700;color:var(--ink);margin-top:44px}
.service-card p{font-size:13px;line-height:1.45;color:var(--muted);margin:10px 36px 0}
.read-more{display:inline-flex;align-items:center;gap:8px;margin-top:14px;font-family:"Orbitron",sans-serif;font-weight:700;font-size:15px;color:var(--ink)}
.service-card.is-active .read-more{color:var(--lime-dark)}
.carousel-arrow{position:absolute;top:370px;width:36px;height:36px;border-radius:50%;border:1px solid #999;background:#fff;display:flex;align-items:center;justify-content:center}

/* gallery */
.gallery{position:absolute;top:3100px;left:0;width:1200px;height:700px;background:linear-gradient(180deg,#ececec,#f7f7f7)}
.gallery .section-title{top:52px}
.gallery-item{position:absolute}
.g1{left:112px;top:160px;width:476px;height:260px;background:linear-gradient(160deg,#3d6a2a,#6a4a2c 60%,#3a2a1a)}
.g2{left:612px;top:160px;width:476px;height:260px;background:linear-gradient(170deg,#7fb0e0,#b48a5a 55%,#7a5a3a)}
.g3{left:112px;top:440px;width:310px;height:260px;background:linear-gradient(170deg,#9fb6c8,#7d6b52 55%,#4a3c2c)}
.g4{left:445px;top:440px;width:310px;height:260px;background:linear-gradient(170deg,#e0a060,#c8a230 55%,#5a4a38)}
.g5{left:778px;top:440px;width:310px;height:260px;background:linear-gradient(170deg,#d8b888,#a87a3a 55%,#4a3a28)}

/* contact */
.contact{position:absolute;top:3840px;left:0;width:1200px;height:560px;background:#fff}
.contact .section-title{top:140px}
.contact-info{position:absolute;left:140px;top:270px;width:300px}
.info-row{display:flex;align-items:flex-start;gap:20px;margin-bottom:34px}
.info-icon{flex:none;width:52px;height:52px;border-radius:50%;background:var(--lime);display:flex;align-items:center;justify-content:center}
.info-row h4{font-family:"Orbitron",sans-serif;font-size:13px;color:var(--ink);font-weight:700;margin-top:4px}
.info-row p{font-size:13.5px;line-height:1.5;color:var(--text);margin-top:4px}
.contact-form{position:absolute;left:476px;top:270px;width:584px}
.form-row{display:flex;gap:12px;margin-bottom:12px}
.field{flex:1;height:44px;border:1px solid var(--line);box-shadow:0 2px 6px rgba(0,0,0,.1);padding:12px 14px;font-size:13px;color:var(--muted)}
.field.message{height:116px}
.contact-form .btn-lime{margin-top:14px;padding:9px 26px;font-size:15px}

/* footer */
.site-footer{position:absolute;top:4400px;left:0;width:1200px;height:656px;background:var(--ink);color:#fff;text-align:center}
.footer-curve{position:absolute;left:0;top:0;width:1200px;height:90px}
.footer-brand{position:absolute;left:0;top:144px;width:1200px;display:flex;align-items:center;justify-content:center;gap:14px;font-family:"Orbitron",sans-serif;font-weight:800;font-size:28px;color:#fff}
.footer-brand .brand-square{width:44px;height:44px}
.footer-nav{position:absolute;top:264px;left:0;width:1200px;display:flex;justify-content:center;gap:68px;font-size:17px;font-weight:600}
.footer-contacts{position:absolute;top:340px;left:184px;display:flex;gap:72px;text-align:left}
.footer-contact{display:flex;align-items:flex-start;gap:12px}
.footer-contact .info-icon{width:40px;height:40px}
.footer-contact h4{font-family:"Orbitron",sans-serif;font-size:13px;font-weight:700}
.footer-contact p{font-size:14px;line-height:1.5;color:#ddd;margin-top:2px}
.socials{display:flex;gap:8px;margin-top:4px}
.socials span{width:26px;height:26px;border-radius:50%;background:var(--lime)}
.footer-divider{position:absolute;left:112px;top:540px;width:976px;height:1px;background:#333}
.copyright{position:absolute;left:112px;top:572px;font-size:14px;color:#ddd}
</style>
</head>
<body>

<header class="site-header">
  <a class="brand" href="#"><span class="brand-square"></span>Bluegum Ridge Earthworks</a>
  <nav class="main-nav">
    <a href="#">Home</a><a href="#">About</a><a href="#">Projects</a><a class="nav-cta" href="#">Contact Us</a>
  </nav>
</header>

<section class="hero">
  <div class="hero-photo" role="img" aria-label="Orange excavator digging into rocky ground under a blue sky"></div>
  <svg class="hero-curve" viewBox="0 0 1200 160" preserveAspectRatio="none">
    <path d="M0 40 Q600 170 1200 40 L1200 160 L0 160 Z" fill="#b2d012"/>
    <path d="M0 80 Q600 180 1200 80 L1200 160 L0 160 Z" fill="#ffffff"/>
  </svg>
  <div class="scroll-cue">
    <svg width="14" height="20" viewBox="0 0 14 20"><rect x="1" y="1" width="12" height="18" rx="6" fill="none" stroke="#0b0b0b" stroke-width="1.6"/><line x1="7" y1="5" x2="7" y2="9" stroke="#0b0b0b" stroke-width="1.6"/></svg>
  </div>
</section>

<section class="about">
  <div class="about-copy">
    <h2>About Bluegum Ridge Earthworks</h2>
    <p>Bluegum Ridge Earthworks was established to deliver a smarter, more professional approach to excavation and earthworking in Perth. Our goal is simple: provide solid groundwork that supports long-lasting results.</p>
    <p>With hands-on industry experience and a strong understanding of local ground conditions, we work closely with clients to ensure each project is completed efficiently and to specification.</p>
    <a class="btn-lime" href="#">Read More</a>
  </div>
  <div class="about-photo a1" role="img" aria-label="Excavator bucket working in a trench"></div>
  <div class="about-photo a2" role="img" aria-label="Yellow excavator on a site at dusk"></div>
  <div class="about-badge"></div>
</section>

<section class="values">
  <div class="section-title"><span class="mark"></span><h2>Our Values</h2></div>
  <div class="value-cards">
    <article class="value-card">
      <div class="value-icon"><svg width="24" height="24" viewBox="0 0 24 24"><circle cx="12" cy="10" r="6" fill="none" stroke="#fff" stroke-width="2"/><path d="M8 15 L6 22 L12 19 L18 22 L16 15" fill="none" stroke="#fff" stroke-width="2"/></svg></div>
      <h3>Quality workmanship</h3>
      <p>Bluegum Ridge Earthworks was smarter, more professional approach to excavation and earthworking</p>
    </article>
    <article class="value-card">
      <div class="value-icon"><svg width="24" height="24" viewBox="0 0 24 24"><path d="M12 2 L20 5 V11 C20 16 16 20 12 22 C8 20 4 16 4 11 V5 Z" fill="none" stroke="#fff" stroke-width="2"/><path d="M8 12 L11 15 L16 9" fill="none" stroke="#fff" stroke-width="2"/></svg></div>
      <h3>Safety-first mindset</h3>
      <p>Bluegum Ridge Earthworks was smarter, more professional approach to excavation and earthworking</p>
    </article>
    <article class="value-card is-active">
      <div class="value-icon"><svg width="24" height="24" viewBox="0 0 24 24"><circle cx="12" cy="8" r="4" fill="none" stroke="#fff" stroke-width="2"/><path d="M4 21 C4 15 20 15 20 21" fill="none" stroke="#fff" stroke-width="2"/></svg></div>
      <h3>Reliability and accountability</h3>
      <p>Bluegum Ridge Earthworks was smarter, more professional approach to excavation and earthworking</p>
    </article>
    <article class="value-card">
      <div class="value-icon"><svg width="24" height="24" viewBox="0 0 24 24"><path d="M3 11 L12 3 L21 11 V21 H3 Z" fill="none" stroke="#fff" stroke-width="2"/><rect x="9" y="14" width="6" height="7" fill="#fff"/></svg></div>
      <h3>Respect for people, property</h3>
      <p>Bluegum Ridge Earthworks was smarter, more professional approach to excavation and earthworking</p>
    </article>
  </div>
  <svg class="values-band" viewBox="0 0 1200 100" preserveAspectRatio="none">
    <path d="M0 100 L0 50 Q600 -10 1200 50 L1200 100 Z" fill="#b2d012"/>
    <path d="M0 100 L0 76 L600 34 L1200 76 L1200 100 Z" fill="#0b0b0b"/>
  </svg>
</section>

<section class="why">
  <div class="section-title on-dark"><h2>Why Choose Us</h2></div>
  <div class="why-mark">Bluegum<br>Ridge</div>
  <div class="why-item left" style="top:190px">
    <div class="why-icon"><svg width="28" height="28" viewBox="0 0 28 28"><path d="M3 20 H18 L22 12 H12 Z M6 20 V24 M18 20 V24" fill="none" stroke="#b2d012" stroke-width="2"/></svg></div>
    <div><h3>General Earthworks</h3><p>Bulk earthworking, soil removal, and final site preparation.</p></div>
  </div>
  <div class="why-item left" style="top:350px">
    <div class="why-icon"><svg width="28" height="28" viewBox="0 0 28 28"><path d="M6 8 H22 L20 24 H8 Z M4 8 H24 M11 4 H17" fill="none" stroke="#b2d012" stroke-width="2"/></svg></div>
    <div><h3>Site Clean-Ups</h3><p>Bulk earthworking, soil removal, and final site preparation.</p></div>
  </div>
  <div class="why-item right" style="top:190px">
    <div class="why-icon"><svg width="28" height="28" viewBox="0 0 28 28"><path d="M4 24 L10 4 M24 24 L18 4 M14 6 V10 M14 14 V18 M14 22 V24" fill="none" stroke="#b2d012" stroke-width="2"/></svg></div>
    <div><h3>Driveways &amp; Hardstands</h3><p>Preparation for concrete driveways, sheds, and access ways.</p></div>
  </div>
  <div class="why-item right" style="top:350px">
    <div class="why-icon"><svg width="28" height="28" viewBox="0 0 28 28"><rect x="4" y="4" width="20" height="20" fill="none" stroke="#b2d012" stroke-width="2"/><path d="M9 14 H19 M14 9 V19" stroke="#b2d012" stroke-width="2"/></svg></div>
    <div><h3>Tight Access Excavation</h3><p>Efficient solutions for restricted or confined spaces.</p></div>
  </div>
</section>

<section class="services">
  <div class="section-title"><span class="mark"></span><h2>Our Services</h2></div>
  <div class="carousel-arrow" style="left:40px"><svg width="10" height="14" viewBox="0 0 10 14"><path d="M8 1 L2 7 L8 13" fill="none" stroke="#333" stroke-width="2"/></svg></div>
  <div class="carousel-arrow" style="left:1124px"><svg width="10" height="14" viewBox="0 0 10 14"><path d="M2 1 L8 7 L2 13" fill="none" stroke="#333" stroke-width="2"/></svg></div>
  <div class="service-cards">
    <article class="service-card">
      <div class="service-photo" role="img" aria-label="Excavator levelling a site"></div>
      <span class="service-icon"></span>
      <h3>Site Cuts &amp; Preparation</h3>
      <p>Accurate site cuts to ensure level, build-ready foundations.</p>
      <a class="read-more" href="#">Read More <svg width="14" height="14" viewBox="0 0 14 14"><circle cx="7" cy="7" r="7" fill="currentColor"/><path d="M5 4 L8 7 L5 10" fill="none" stroke="#fff" stroke-width="1.6"/></svg></a>
    </article>
    <article class="service-card is-active">
      <div class="service-photo" role="img" aria-label="Pipes laid in an open trench"></div>
      <span class="service-icon"></span>
      <h3>Trenching &amp; Services</h3>
      <p>Precise trenching for plumbing, electrical, and drainage services.</p>
      <a class="read-more" href="#">Read More <svg width="14" height="14" viewBox="0 0 14 14"><circle cx="7" cy="7" r="7" fill="currentColor"/><path d="M5 4 L8 7 L5 10" fill="none" stroke="#fff" stroke-width="1.6"/></svg></a>
    </article>
    <article class="service-card">
      <div class="service-photo" role="img" aria-label="Excavator digging footings at sunset"></div>
      <span class="service-icon"></span>
      <h3>Footings &amp; Foundations</h3>
      <p>Clean, accurate excavation for footings and structural foundations.</p>
      <a class="read-more" href="#">Read More <svg width="14" height="14" viewBox="0 0 14 14"><circle cx="7" cy="7" r="7" fill="currentColor"/><path d="M5 4 L8 7 L5 10" fill="none" stroke="#fff" stroke-width="1.6"/></svg></a>
    </article>
  </div>
</section>

<section class="gallery">
  <div class="section-title"><span class="mark"></span><h2>Our Gallery</h2></div>
  <div class="gallery-item g1" role="img" aria-label="Shovel turning dark soil"></div>
  <div class="gallery-item g2" role="img" aria-label="Excavator beside a house under construction"></div>
  <div class="gallery-item g3" role="img" aria-label="Excavator on a cleared earth pad"></div>
  <div class="gallery-item g4" role="img" aria-label="Yellow hard hat on a building site at sunset"></div>
  <div class="gallery-item g5" role="img" aria-label="Loader moving dirt in a dusty yard"></div>
</section>

<section class="contact">
  <div class="section-title"><span class="mark"></span><h2>contact us</h2></div>
  <div class="contact-info">
    <div class="info-row">
      <div class="info-icon"><svg width="22" height="22" viewBox="0 0 24 24"><rect x="3" y="5" width="18" height="14" fill="none" stroke="#fff" stroke-width="2"/><path d="M3 6 L12 13 L21 6" fill="none" stroke="#fff" stroke-width="2"/></svg></div>
      <div><h4>EMAIL:</h4><p>hello@bluegumridge.example</p></div>
    </div>
    <div class="info-row">
      <div class="info-icon"><svg width="22" height="22" viewBox="0 0 24 24"><path d="M5 3 H9 L11 8 L8 10 C9 13 11 15 14 16 L16 13 L21 15 V19 C21 20 20 21 19 21 C10 21 3 14 3 5 C3 4 4 3 5 3 Z" fill="#fff"/></svg></div>
      <div><h4>PHONE:</h4><p>+61 8 9000 4417</p></div>
    </div>
    <div class="info-row">
      <div class="info-icon"><svg width="22" height="22" viewBox="0 0 24 24"><path d="M12 22 C12 22 5 14 5 9 A7 7 0 0 1 19 9 C19 14 12 22 12 22 Z" fill="#fff"/><circle cx="12" cy="9" r="2.5" fill="#b2d012"/></svg></div>
      <div><h4>ADDRESS:</h4><p>14 Quarry Lane,<br>Welshpool, WA 6106</p></div>
    </div>
  </div>
  <form class="contact-form">
    <div class="form-row"><div class="field">First Name</div><div class="field">Last Name</div></div>
    <div class="form-row"><div class="field">Phone Number</div><div class="field">Email</div></div>
    <div class="form-row"><div class="field message">Message</div></div>
    <span class="btn-lime">Submit</span>
  </form>
</section>

<footer class="site-footer">
  <svg class="footer-curve" viewBox="0 0 1200 90" preserveAspectRatio="none">
    <path d="M0 0 H1200 V20 Q600 110 0 20 Z" fill="#ffffff"/>
    <path d="M0 20 Q600 110 1200 20" fill="none" stroke="#b2d012" stroke-width="6"/>
  </svg>
  <div class="footer-brand"><span class="brand-square"></span>Bluegum Ridge Earthworks</div>
  <nav class="footer-nav"><a href="#">HOME</a><a href="#">ABOUT US</a><a href="#">SERVICE</a><a href="#">PROJECTS</a><a href="#">CONTACT US</a></nav>
  <div class="footer-contacts">
    <div class="footer-contact">
      <div class="info-icon"><svg width="18" height="18" viewBox="0 0 24 24"><path d="M5 3 H9 L11 8 L8 10 C9 13 11 15 14 16 L16 13 L21 15 V19 C21 20 20 21 19 21 C10 21 3 14 3 5 C3 4 4 3 5 3 Z" fill="#fff"/></svg></div>
      <div><h4>PHONE:</h4><p>08 9000 4417</p></div>
    </div>
    <div class="footer-contact">
      <div class="info-icon"><svg width="18" height="18" viewBox="0 0 24 24"><rect x="3" y="5" width="18" height="14" fill="none" stroke="#fff" stroke-width="2"/><path d="M3 6 L12 13 L21 6" fill="none" stroke="#fff" stroke-width="2"/></svg></div>
      <div><h4>E-MAIL:</h4><p>hello@bluegumridge.example</p><div class="socials"><span></span><span></span><span></span><span></span></div></div>
    </div>
    <div class="footer-contact">
      <div class="info-icon"><svg width="18" height="18" viewBox="0 0 24 24"><path d="M12 22 C12 22 5 14 5 9 A7 7 0 0 1 19 9 C19 14 12 22 12 22 Z" fill="#fff"/><circle cx="12" cy="9" r="2.5" fill="#b2d012"/></svg></div>
      <div><h4>ADDRESS :</h4><p>14 Quarry Lane Welshpool<br>WA 6106 Australia</p></div>
    </div>
  </div>
  <div class="footer-divider"></div>
  <p class="copyright">Copyright © 2025 Company Name. All Rights Reserved</p>
</footer>

</body>
</html>
```